eBook Cover_H. Lindqvist-Borna
Schnell und zuverlässoig,Änderungswünsche wurden umgehend ausgeführt. Vielen Dank für das tolle Cover zu meinem ersten Buch!
Zielgruppe
freie Roman-Autorin (Erstlingswerk)
Zielgruppe: Lesende (Erwachsene), Frauen
Charakterisierung: magisch-realistischer Familienroman, spielt im Europa der Jetzt-Zeit
Aufgabenstellung
Im ersten Schritt geht es um ein Cover für ein eBook, das aber bei Bedarf als Book on Demand gedruckt werden soll. Es wird daher später Anforderung bzgl. Dicke / Umfang des gedruckten Buches und einer Rückseite geben. Das gewählte Design soll dann dahingehend überarbeitet und finale Druckdaten zur Verfügung gestellt werden. Dies soll von vornherein berücksichtigt werden und im Preis enthalten sein.
Titel: Regen über Glas, Monde im Moos
Autorinnenname: Henrike Lindqvist-Borna
des weiteren auf dem Cover: Roman

```html
<!DOCTYPE html>
<html lang="de">
<head>
<meta charset="utf-8">
<title>Regen über Glas, Monde im Moos – Henrike Lindqvist-Borna</title>
<link rel="stylesheet" href="https://fonts.googleapis.com/css2?family=Cinzel:wght@600;700&display=swap">
<style>
  :root {
    --page: #ffffff;
    --night-deep: #0c1530;
    --night-blue: #2b3f7e;
    --haze-blue: #6f86b8;
    --glow-warm: #f3d2b4;
    --glow-rose: #e7b9a6;
    --ridge: #0a0a0d;
    --type: #ffffff;
    --type-edge: rgba(10, 16, 40, 0.75);
  }
  * { margin: 0; padding: 0; box-sizing: border-box; }
  html, body {
    width: 848px;
    height: 1200px;
    overflow: hidden;
    background: var(--page);
  }
  .page {
    position: relative;
    width: 848px;
    height: 1200px;
    background: var(--page);
  }
  .cover {
    position: absolute;
    left: 127px;
    top: 107px;
    width: 606px;
    height: 895px;
    overflow: hidden;
    font-family: "Cinzel", "Times New Roman", serif;
    color: var(--type);
  }
  .cover-art {
    position: absolute;
    inset: 0;
    background:
      radial-gradient(ellipse 60% 45% at 55% 80%, var(--glow-warm) 0%, rgba(231,185,166,0.55) 35%, rgba(111,134,184,0) 75%),
      linear-gradient(180deg, var(--night-deep) 0%, var(--night-blue) 30%, var(--haze-blue) 58%, var(--glow-rose) 82%, var(--ridge) 94%, var(--ridge) 100%);
  }
  .cover-text {
    position: absolute;
    left: 0;
    width: 100%;
    text-align: center;
    text-shadow: 0 0 2px var(--type-edge), 0 1px 3px var(--type-edge);
  }
  .author {
    top: 35px;
    font-size: 26px;
    font-weight: 700;
    letter-spacing: 0.5px;
  }
  .title {
    top: 128px;
    font-size: 64px;
    font-weight: 700;
    line-height: 70px;
    letter-spacing: 0.5px;
  }
  .title .link-word {
    font-size: 30px;
    letter-spacing: 0;
  }
  .genre {
    top: 828px;
    font-size: 25px;
    font-weight: 600;
    letter-spacing: 1px;
  }
</style>
</head>
<body>
  <main class="page">
    <section class="cover">
      <div class="cover-art" role="img" aria-label="Sternenhimmel mit Milchstraße über einem dunklen Berggrat, auf dem die Silhouette einer Frau mit erhobenem Arm steht"></div>
      <p class="cover-text author">Henrike Lindqvist-Borna</p>
      <h1 class="cover-text title">
        Regen <span class="link-word">über</span> Glas,<br>
        Monde <span class="link-word">im</span> Moos
      </h1>
      <p class="cover-text genre">Roman</p>
    </section>
  </main>
</body>
</html>
```